indépendant en tant que Massothérapeute et Préparateur Mental, j'ai besoin de ...

Massothérapeute et préparateur mental indépendant, je recherche une carte de visite sobre et dynamique, sans images liées au massage ou à la préparation mentale mais intégrant mon logo. Les couleurs que j'aime bien sont : Blanc, gris, anthracite, noir et jaune

Contact Information for Business Card

carte de préférence Horizontale
neutre qui puisse toucher le deux domaines Massothérapie et préparation mentale

Requirements
Must have
• mon projet doit intégrer au recto:
LOGO
Loïc Bardèze
078 513 26 48
info@loicbardeze.ch
et éventuellement www.loicbardeze.ch

et au verso les deux adresses:

Chemin des Ormilles 7B
1400 Yverdon-les-Bains

Route de la Gravière 9
1700 Fribourg

Should not have
• mon projet ne doit pas contenir d'image en liens avec le massage ni la préparation mentale.

```html
<!DOCTYPE html>
<html lang="fr">
<head>
<meta charset="utf-8">
<title>Carte de visite – Loïc Bardèze</title>
<link href="https://fonts.googleapis.com/css2?family=Montserrat:wght@400;500;700&family=Arimo:wght@400&display=swap" rel="stylesheet">
<style>
  :root {
    --stage: #2a2a2a;
    --anthracite: #222122;
    --white: #ffffff;
    --yellow: #e8c800;
    --ink: #232323;
  }
  * { box-sizing: border-box; margin: 0; padding: 0; }
  html, body { width: 1200px; height: 1015px; overflow: hidden; }
  body {
    background: var(--stage);
    position: relative;
    font-family: "Arimo", Arial, sans-serif;
  }
  .card {
    position: absolute;
    left: 300px;
    width: 600px;
    height: 370px;
    background: var(--anthracite);
    overflow: hidden;
    box-shadow: 0 10px 28px rgba(0,0,0,.45);
  }
  .card--back { top: 90px; }
  .card--front { top: 545px; }
  .card__shape { position: absolute; inset: 0; }

  .brand {
    position: absolute;
    left: 318px;
    top: 100px;
    color: var(--ink);
  }
  .brand__name {
    display: flex;
    align-items: center;
    gap: 10px;
    font-family: "Montserrat", sans-serif;
    font-weight: 700;
    font-size: 28px;
    letter-spacing: .3px;
    white-space: nowrap;
  }
  .brand__dot {
    width: 18px; height: 18px;
    border-radius: 50%;
    background: var(--ink);
    flex: none;
  }
  .brand__tagline {
    margin-top: 8px;
    margin-left: 28px;
    font-family: "Montserrat", sans-serif;
    font-weight: 500;
    font-size: 9px;
    letter-spacing: .8px;
    text-transform: uppercase;
    white-space: nowrap;
  }

  .addresses {
    position: absolute;
    left: 48px;
    top: 130px;
    color: var(--white);
    font-size: 16px;
    line-height: 1.3;
  }
  .addresses__block + .addresses__block { margin-top: 22px; }

  .contact {
    position: absolute;
    left: 48px;
    top: 192px;
    color: var(--white);
  }
  .contact__name {
    font-family: "Montserrat", sans-serif;
    font-weight: 700;
    font-size: 24px;
    color: var(--yellow);
    letter-spacing: .5px;
    margin-bottom: 18px;
    white-space: nowrap;
  }
  .contact__list { list-style: none; font-size: 16px; line-height: 1.45; }
  .contact__item { display: flex; align-items: center; gap: 9px; }
  .contact__icon { width: 15px; height: 15px; flex: none; }
</style>
</head>
<body>

<section class="card card--back" aria-label="Verso de la carte">
  <svg class="card__shape" viewBox="0 0 600 370" aria-hidden="true">
    <circle cx="480" cy="110" r="230" fill="var(--white)"/>
    <path d="M273 35 A220 220 0 0 0 442 327" fill="none" stroke="var(--yellow)" stroke-width="3"/>
  </svg>
  <div class="brand">
    <div class="brand__name"><span class="brand__dot"></span>Loïc Bardèze</div>
    <div class="brand__tagline">Massothérapeute / Préparateur mental</div>
  </div>
  <div class="addresses">
    <p class="addresses__block">Chemin des Ormilles 7B<br>1400 Yverdon-les-Bains</p>
    <p class="addresses__block">Route de la Gravière 9<br>1700 Freiburg</p>
  </div>
</section>

<section class="card card--front" aria-label="Recto de la carte">
  <svg class="card__shape" viewBox="0 0 600 370" aria-hidden="true">
    <circle cx="480" cy="110" r="230" fill="var(--white)"/>
    <path d="M273 35 A220 220 0 0 0 442 327" fill="none" stroke="var(--yellow)" stroke-width="3"/>
  </svg>
  <div class="brand">
    <div class="brand__name"><span class="brand__dot"></span>Loïc Bardèze</div>
    <div class="brand__tagline">Massothérapeute / Préparateur mental</div>
  </div>
  <div class="contact">
    <h1 class="contact__name">LOÏC BARDÈZE</h1>
    <ul class="contact__list">
      <li class="contact__item">
        <svg class="contact__icon" viewBox="0 0 16 16" aria-hidden="true"><path d="M3 1.5l2.5 0 1.2 3-1.6 1.2a8 8 0 0 0 5.2 5.2l1.2-1.6 3 1.2v2.5c0 .8-.7 1.5-1.5 1.5A12.5 12.5 0 0 1 1.5 3c0-.8.7-1.5 1.5-1.5z" fill="var(--yellow)"/></svg>
        078 513 26 48
      </li>
      <li class="contact__item">
        <svg class="contact__icon" viewBox="0 0 16 16" aria-hidden="true"><rect x="1" y="3" width="14" height="10" fill="var(--yellow)"/><path d="M1 3l7 6 7-6" fill="none" stroke="var(--anthracite)" stroke-width="1.3"/></svg>
        info@loicbardeze.ch
      </li>
      <li class="contact__item">
        <svg class="contact__icon" viewBox="0 0 16 16" aria-hidden="true"><g fill="none" stroke="var(--yellow)" stroke-width="1.4"><circle cx="8" cy="8" r="6.5"/><ellipse cx="8" cy="8" rx="2.8" ry="6.5"/><path d="M1.5 8h13M2.5 5h11M2.5 11h11"/></g></svg>
        www.loicbardeze.ch
      </li>
    </ul>
  </div>
</section>

</body>
</html>
```